Boutique town planning business needs a Business Card design

We need a business card design for a new company called The Zoning Bridgeway. We provide town planning and urban design services to government, business and community groups. We would like to see the designs use the colours in the logo (blue, deep red, green and amber), plenty of white and including black and grey in the writing. The final design should communicate collaboration, creativity and professionalism and that we are approachable.

Industry/Entity Type

Town

```html
<!DOCTYPE html>
<html lang="en">
<head>
<meta charset="utf-8">
<title>The Zoning Bridgeway — Business Card</title>
<link href="https://fonts.googleapis.com/css2?family=Exo+2:wght@400;600&display=swap" rel="stylesheet">
<style>
  :root {
    --page-bg: #ececec;
    --card-white: #ffffff;
    --card-grey: #f1f1f1;
    --panel-black: #000000;
    --accent-red: #9a5a52;
    --text-light: #f2f2f2;
    --text-dark: #5f6468;
    --mark-blue: #2aa3c8;
  }
  * { margin: 0; padding: 0; box-sizing: border-box; }
  html, body { width: 1200px; height: 905px; overflow: hidden; }
  body {
    background: var(--page-bg);
    font-family: "Exo 2", sans-serif;
    display: flex;
    align-items: center;
    justify-content: center;
    gap: 40px;
  }
  .card {
    width: 560px;
    height: 320px;
    position: relative;
    overflow: hidden;
    box-shadow: 0 2px 6px rgba(0,0,0,0.12);
  }
  .card-front { display: flex; background: var(--card-grey); }
  .contact-panel {
    width: 60%;
    height: 100%;
    background: var(--panel-black);
    color: var(--text-light);
    position: relative;
    padding: 60px 24px 0 30px;
  }
  .accent-tab {
    position: absolute;
    top: 0;
    right: 0;
    width: 30px;
    height: 48px;
    background: var(--accent-red);
  }
  .person-name {
    font-size: 17px;
    font-weight: 400;
    letter-spacing: 0.06em;
    text-transform: uppercase;
  }
  .person-role {
    font-size: 16px;
    margin-top: 4px;
    letter-spacing: 0.03em;
  }
  .contact-grid {
    display: grid;
    grid-template-columns: auto auto;
    column-gap: 16px;
    row-gap: 10px;
    margin-top: 44px;
    font-size: 10.5px;
    letter-spacing: 0.04em;
  }
  .contact-item { display: flex; align-items: center; gap: 6px; white-space: nowrap; }
  .contact-item svg { width: 11px; height: 11px; fill: var(--text-light); flex: none; }
  .address {
    margin-top: 14px;
    font-size: 13.5px;
    letter-spacing: 0.05em;
    white-space: nowrap;
  }
  .brand-panel {
    flex: 1;
    display: flex;
    align-items: center;
    justify-content: center;
  }
  .card-back {
    background: var(--card-white);
    display: flex;
    align-items: center;
    justify-content: center;
  }
  .brand {
    display: flex;
    align-items: center;
    gap: 10px;
  }
  .brand-dot {
    width: 40px;
    height: 40px;
    border-radius: 50%;
    background: var(--mark-blue);
    flex: none;
  }
  .brand-name {
    font-size: 19px;
    font-weight: 600;
    color: var(--text-dark);
    line-height: 1.1;
  }
</style>
</head>
<body>
  <section class="card card-front" aria-label="Business card front">
    <div class="contact-panel">
      <div class="accent-tab"></div>
      <p class="person-name">Tobin Ashgrove</p>
      <p class="person-role">Managing Director</p>
      <div class="contact-grid">
        <div class="contact-item">
          <svg viewBox="0 0 12 12"><rect x="1" y="4" width="10" height="7" rx="1"/><rect x="3" y="1" width="6" height="3"/></svg>
          020 555 0147
        </div>
        <div class="contact-item">
          <svg viewBox="0 0 12 12"><rect x="1" y="2.5" width="10" height="7"/></svg>
          hello@zoningbridge.com
        </div>
        <div class="contact-item">
          <svg viewBox="0 0 12 12"><path d="M3 1l2 2.5-1.2 1.5a7 7 0 0 0 3.2 3.2L8.5 7 11 9l-1.5 2C5 11 1 7 1 2.5z"/></svg>
          020 555 0147
        </div>
        <div class="contact-item">
          <svg viewBox="0 0 12 12"><circle cx="6" cy="6" r="5" fill="none" stroke="#f2f2f2" stroke-width="1.2"/><path d="M1 6h10M6 1v10" stroke="#f2f2f2" stroke-width="1"/></svg>
          www.zoningbridge.com
        </div>
      </div>
      <p class="address">41 6th floor Harbour Lane Road NTH</p>
    </div>
    <div class="brand-panel">
      <div class="brand">
        <span class="brand-dot"></span>
        <span class="brand-name">The Zoning<br>Bridgeway</span>
      </div>
    </div>
  </section>

  <section class="card card-back" aria-label="Business card back">
    <div class="brand">
      <span class="brand-dot"></span>
      <span class="brand-name">The Zoning<br>Bridgeway</span>
    </div>
  </section>
</body>
</html>
```